New Fun, Positive, energised looking Business Card Needed for High Achiever Coach

I am looking for a two sided full colour business card. I am self employed and have recently re branded my 1-2-1 work Renewing Driven Leaders. My target client base for these cards is therefore high achievers - usually aged 40 -55, they are often entrepreneurs, CEO or work in banking and finance and 2/3 are male. I work with them on 90 day or 6 month coaching programs to help them live their success in a healthier, more sustainable and fulfiiled way. They pay for this privately so though they are corporate types the cards need not look 'corporate'. I want to portray the idea of transformation, vitality and re-connecting.
You can get a feel for the look I like on my new website: morvenlisk.co.uk
I want to use this logo with strapline (Renewing Driven Leaders) (I purchased off Logoharbor) and font/ colours (the turquoise and green).
Details to include on the card:
www.morvenlisk.co.uk
+44 7915 302618
morven@morvenlisk.co.uk
skype: morvenlisk
I'd also like to include:
Do you struggle to switch off? Want to be healthier and feel fitter? Want closer relationships? More clarity over the direction you are headed? I can help you do these things using integrated mind-body techniques. Visit morvenlisk.co.uk TODAY to apply for a FREE Breakthrough session.
BUT if that is too much text for a card I am open to advice/ammendments.
Updates
Thanks for your design - I am considering them. PLease change the wording to :

```html
<!DOCTYPE html>
<html lang="en">
<head>
<meta charset="utf-8">
<title>Morven Lisk – Business Card Options</title>
<link rel="stylesheet" href="https://fonts.googleapis.com/css2?family=Open+Sans:wght@400;600;700;800&display=swap">
<style>
  :root {
    --backdrop: #6a3d29;
    --card: #000000;
    --turquoise: #00a3c7;
    --green: #5dbb6a;
    --white: #ffffff;
    --divider: #d8d8d8;
    --chip: #7d8a99;
    --label: #ffffff;
  }
  * { box-sizing: border-box; margin: 0; padding: 0; }
  html, body {
    width: 1200px; height: 807px; overflow: hidden;
    background: var(--backdrop);
    font-family: "Open Sans", Arial, sans-serif;
  }
  .board { position: relative; width: 1200px; height: 807px; }

  .option-label {
    position: absolute;
    color: var(--label);
    font-size: 33px;
    font-weight: 400;
    transform: translateX(-50%);
    line-height: 1;
  }

  .card {
    position: absolute;
    width: 482px; height: 276px;
    background: var(--card);
    overflow: hidden;
    color: var(--white);
  }
  .card-band { position: absolute; inset: 0; width: 100%; height: 100%; }

  .brand {
    position: absolute;
    left: 26px; top: 128px;
    width: 204px;
    text-align: center;
  }
  .brand-name {
    color: var(--turquoise);
    font-weight: 800;
    font-size: 22px;
    line-height: 1.1;
  }
  .brand-strapline {
    color: var(--turquoise);
    font-size: 10.5px;
    margin-top: 3px;
  }

  .divider {
    position: absolute;
    left: 230px; top: 44px;
    width: 2px; height: 122px;
    background: linear-gradient(to bottom, transparent, var(--divider) 30%, var(--divider) 70%, transparent);
  }

  .contact-list {
    position: absolute;
    left: 249px; top: 64px;
    list-style: none;
  }
  .contact-list li {
    display: flex; align-items: center;
    font-size: 16px;
    height: 20px;
    margin-bottom: 13px;
    white-space: nowrap;
  }
  .contact-icon { width: 13px; height: 13px; margin-right: 6px; flex: none; }

  .follow { font-size: 13.5px; }
  .social-chips { display: flex; gap: 4px; margin-left: 6px; }
  .social-chip {
    width: 15px; height: 15px;
    background: var(--chip);
    border-radius: 2px;
  }

  .website {
    position: absolute;
    right: 26px; bottom: 17px;
    font-weight: 700;
    font-size: 16.5px;
    letter-spacing: 0.3px;
  }
  .follow-corner {
    position: absolute;
    right: 26px; bottom: 12px;
    text-align: right;
    font-size: 13.5px;
  }
  .follow-corner .social-chips { justify-content: flex-end; margin: 7px 0 0; }

  .card-back { text-align: center; }
  .back-copy {
    position: absolute;
    left: 0; right: 0; top: 50px;
    font-size: 15px;
    line-height: 20px;
  }
  .back-copy p + p { margin-top: 10px; }
  .back-copy strong { font-weight: 700; }
</style>
</head>
<body>
<main class="board">

  <span class="option-label" style="left:315px; top:56px;">Option#1</span>
  <span class="option-label" style="left:873px; top:56px;">Option#2</span>
  <span class="option-label" style="left:315px; top:718px;">Option#3</span>

  <section class="card card-front" style="left:103px; top:107px;">
    <svg class="card-band" viewBox="0 0 482 276" preserveAspectRatio="none" aria-hidden="true">
      <polygon points="0,236 482,206 482,211 0,241" fill="var(--green)"/>
      <polygon points="0,248 482,218 482,276 0,276" fill="var(--turquoise)"/>
    </svg>
    <div class="brand">
      <div class="brand-name">Morven Lisk</div>
      <div class="brand-strapline">Renewing Driven Leaders</div>
    </div>
    <div class="divider"></div>
    <ul class="contact-list">
      <li><svg class="contact-icon" viewBox="0 0 16 16"><path d="M4 1 L6.5 4 L5 6 C6 8.5 7.5 10 10 11 L12 9.5 L15 12 L13 15 C7 14.5 1.5 9 1 3 Z" fill="var(--white)"/></svg>+44 7915 302618</li>
      <li><svg class="contact-icon" viewBox="0 0 16 16"><rect x="1" y="4" width="14" height="10" rx="1" fill="var(--white)"/><path d="M1 5 L8 10 L15 5" stroke="var(--card)" stroke-width="1.3" fill="none"/></svg>morven@morvenlisk.co.uk</li>
      <li><span class="social-chip contact-icon"></span>morvenlisk</li>
    </ul>
    <div class="website">www.morvenlisk.co.uk</div>
  </section>

  <section class="card card-front" style="left:622px; top:108px;">
    <svg class="card-band" viewBox="0 0 482 276" preserveAspectRatio="none" aria-hidden="true">
      <polygon points="0,236 482,206 482,211 0,241" fill="var(--green)"/>
      <polygon points="0,248 482,218 482,276 0,276" fill="var(--turquoise)"/>
    </svg>
    <div class="brand">
      <div class="brand-name">Morven Lisk</div>
      <div class="brand-strapline">Renewing Driven Leaders</div>
    </div>
    <div class="divider"></div>
    <ul class="contact-list">
      <li><svg class="contact-icon" viewBox="0 0 16 16"><path d="M4 1 L6.5 4 L5 6 C6 8.5 7.5 10 10 11 L12 9.5 L15 12 L13 15 C7 14.5 1.5 9 1 3 Z" fill="var(--white)"/></svg>+44 7915 302618</li>
      <li><svg class="contact-icon" viewBox="0 0 16 16"><rect x="1" y="4" width="14" height="10" rx="1" fill="var(--white)"/><path d="M1 5 L8 10 L15 5" stroke="var(--card)" stroke-width="1.3" fill="none"/></svg>morven@morvenlisk.co.uk</li>
      <li class="follow">Follow us on
        <span class="social-chips"><span class="social-chip"></span><span class="social-chip"></span><span class="social-chip"></span><span class="social-chip"></span></span>
      </li>
    </ul>
    <div class="website">www.morvenlisk.co.uk</div>
  </section>

  <section class="card card-front" style="left:104px; top:419px;">
    <svg class="card-band" viewBox="0 0 482 276" preserveAspectRatio="none" aria-hidden="true">
      <polygon points="0,236 482,206 482,211 0,241" fill="var(--green)"/>
      <polygon points="0,248 482,218 482,276 0,276" fill="var(--turquoise)"/>
    </svg>
    <div class="brand">
      <div class="brand-name">Morven Lisk</div>
      <div class="brand-strapline">Renewing Driven Leaders</div>
    </div>
    <div class="divider"></div>
    <ul class="contact-list">
      <li><svg class="contact-icon" viewBox="0 0 16 16"><path d="M4 1 L6.5 4 L5 6 C6 8.5 7.5 10 10 11 L12 9.5 L15 12 L13 15 C7 14.5 1.5 9 1 3 Z" fill="var(--white)"/></svg>+44 7915 302618</li>
      <li><svg class="contact-icon" viewBox="0 0 16 16"><rect x="1" y="4" width="14" height="10" rx="1" fill="var(--white)"/><path d="M1 5 L8 10 L15 5" stroke="var(--card)" stroke-width="1.3" fill="none"/></svg>morven@morvenlisk.co.uk</li>
      <li><svg class="contact-icon" viewBox="0 0 16 16"><circle cx="8" cy="8" r="6.3" stroke="var(--white)" stroke-width="1.3" fill="none"/><ellipse cx="8" cy="8" rx="2.8" ry="6.3" stroke="var(--white)" stroke-width="1.1" fill="none"/><path d="M2 8 H14 M3 5 H13 M3 11 H13" stroke="var(--white)" stroke-width="1"/></svg>www.morvenlisk.co.uk</li>
    </ul>
    <div class="follow-corner">
      Follow us on
      <div class="social-chips"><span class="social-chip"></span><span class="social-chip"></span><span class="social-chip"></span><span class="social-chip"></span></div>
    </div>
  </section>

  <section class="card card-back" style="left:629px; top:419px;">
    <div class="back-copy">
      <p>Finding it hard to unwind?<br>
      Hoping to feel stronger and healthier?<br>
      Looking for deeper connections?<br>
      Seeking a clearer sense of where you are going?</p>
      <p>Together we can get there with joined-up<br>mind and body methods.</p>
      <p>Go to <strong>morvenlisk.co.uk</strong> NOW and book your<br>FREE Breakthrough session.</p>
    </div>
  </section>

</main>
</body>
</html>
```